Melorix artwork for new single release

I need Melorix artwork creating to release a new single on there.

The specs are:

Ideal size: 3000 x 3000 pixels
Minimum size: 1400 x 1400 pixels
Aspect ratio: 1:1 (must be a perfect square)
File format: JPG or PNG
Color space: sRGB
File size: Max 4MB

The song is called "Was It Ever Rain?"
The artist is "Martin Hollow"

We have no images of Martin, so it really is open to imagination.

Target Market(s)

Melorix listeners

Industry/Entity Type

Music

```html
<!DOCTYPE html>
<html lang="en">
<head>
<meta charset="utf-8">
<title>Was It Ever Rain? — Martin Hollow</title>
<link rel="stylesheet" href="https://fonts.googleapis.com/css2?family=Oswald:wght@300;500&display=swap">
<style>
  :root {
    --sky-top: #0b1e2c;
    --sky-mid: #1d4b5c;
    --sky-glow: #6f9aa4;
    --horizon: #c99a8e;
    --city-light: #e08a3a;
    --water: #2a3340;
    --pavement: #3a2a2a;
    --pavement-dark: #1a1416;
    --title: #f9a43c;
    --title-glow: rgba(255, 150, 40, 0.65);
    --artist: #ffffff;
  }
  * { margin: 0; padding: 0; box-sizing: border-box; }
  html, body {
    width: 1200px;
    height: 1200px;
    overflow: hidden;
    background: var(--sky-top);
  }
  .cover {
    position: relative;
    width: 1200px;
    height: 1200px;
    overflow: hidden;
  }
  .cover-scene {
    position: absolute;
    inset: 0;
    background:
      radial-gradient(ellipse 30% 40% at 50% 62%, rgba(235, 120, 50, 0.35), transparent 70%),
      linear-gradient(to bottom,
        var(--sky-top) 0%,
        var(--sky-mid) 30%,
        var(--sky-glow) 40%,
        var(--horizon) 45%,
        var(--city-light) 48%,
        var(--water) 55%,
        #3c3f4c 68%,
        var(--water) 76%,
        var(--pavement) 80%,
        var(--pavement-dark) 100%);
  }
  .release-title {
    position: absolute;
    top: 128px;
    left: 0;
    width: 100%;
    text-align: center;
    font-family: "Oswald", sans-serif;
    font-weight: 500;
    font-size: 142px;
    line-height: 1;
    letter-spacing: 0.02em;
    text-transform: uppercase;
    color: var(--title);
    text-shadow: 0 0 14px var(--title-glow), 0 0 34px rgba(255, 130, 30, 0.35);
  }
  .artist-name {
    position: absolute;
    top: 1036px;
    left: 0;
    width: 100%;
    text-align: center;
    font-family: "Oswald", sans-serif;
    font-weight: 300;
    font-size: 64px;
    line-height: 1;
    letter-spacing: 0.62em;
    padding-left: 0.62em;
    text-transform: uppercase;
    color: var(--artist);
  }
</style>
</head>
<body>
  <main class="cover">
    <div class="cover-scene" role="img" aria-label="Night photograph of a man in silhouette standing on a cobbled riverside walk, hand on a glowing heart on his chest, under a starry sky with city lights reflected in the river"></div>
    <h1 class="release-title">Was It Ever Rain?</h1>
    <p class="artist-name">Martin Hollow</p>
  </main>
</body>
</html>
```